Computer Training in the Education sector - Letterhead

We need a new letter head to be designed for the company. We provide computer training fro the Education Sector, both primary and private tertiary providers. The colours will need to tie in with the website www.crossingthestream.co.nz.
The company name is Crossing the Stream with the tag line of Computer Training for Educators.
The footer will need to have the following detail...
0508 PCS MENTOR
021 839 415
www.crossingthestream.co.nz / training@crossingthestream.co.nz
Updates

Thanks for the designs so far.

Some have watermarks in the background. Please don't worry about using watermarks as I will not be using a watermark in in a final design.
Regards,
Roger

Thank you for all the designs and the effort. There was some great concepts that came through.

Cheers
Roger

Industry/Entity Type

Computer

```html
<!DOCTYPE html>
<html lang="en">
<head>
<meta charset="utf-8">
<title>Crossing the Stream – Letterhead</title>
<link rel="stylesheet" href="https://fonts.googleapis.com/css2?family=Open+Sans:wght@400;600&display=swap">
<style>
  :root {
    --backdrop: #e8e8e8;
    --sky-top: #d4ecf6;
    --sky-bottom: #ffffff;
    --brand-blue: #3a7cc4;
    --brand-orange: #f28c28;
    --rule-orange: #f0a24a;
    --label-green: #5aa832;
    --grass-light: #9ad14b;
    --grass-mid: #5fae2a;
    --grass-dark: #3e8a1e;
  }
  * { box-sizing: border-box; margin: 0; padding: 0; }
  html, body {
    width: 1200px;
    height: 795px;
    overflow: hidden;
    background: var(--backdrop);
    font-family: "Open Sans", Arial, sans-serif;
  }
  .letterhead {
    position: absolute;
    left: 340px;
    top: 25px;
    width: 520px;
    height: 745px;
    background: linear-gradient(to bottom, var(--sky-top) 0%, #e9f5fa 45%, var(--sky-bottom) 85%);
    box-shadow: 0 6px 20px rgba(0, 0, 0, 0.12);
    overflow: hidden;
  }
  .brand {
    position: absolute;
    left: 44px;
    top: 48px;
    display: flex;
    align-items: center;
    gap: 10px;
  }
  .brand-mark {
    width: 34px;
    height: 34px;
    border-radius: 50%;
    background: var(--label-green);
    flex: none;
  }
  .brand-name {
    font-size: 19px;
    font-weight: 600;
    color: var(--brand-blue);
    line-height: 1.1;
  }
  .tagline {
    position: absolute;
    left: 44px;
    top: 96px;
    font-size: 9.5px;
    color: var(--brand-blue);
    letter-spacing: 0.2px;
  }
  .header-rule {
    position: absolute;
    left: 0;
    right: 0;
    top: 150px;
    height: 1.5px;
    background: var(--rule-orange);
  }
  .grass {
    position: absolute;
    left: 0;
    right: 0;
    bottom: 0;
    height: 170px;
    background: linear-gradient(to top, var(--grass-dark) 0%, var(--grass-mid) 45%, var(--grass-light) 100%);
    clip-path: polygon(0 100%, 0 96%, 40% 93%, 78% 86%, 88% 55%, 100% 0, 100% 100%);
    z-index: 0;
  }
  .contact {
    position: absolute;
    left: 44px;
    bottom: 46px;
    z-index: 1;
    font-size: 9.5px;
    line-height: 1.45;
    color: var(--brand-blue);
  }
  .contact .phone { color: var(--brand-orange); }
  .contact .label { color: var(--label-green); margin-right: 3px; }
  .contact .sep { margin-right: 8px; }
</style>
</head>
<body>
  <main class="letterhead">
    <header>
      <div class="brand">
        <span class="brand-mark"></span>
        <span class="brand-name">Crossing the Stream</span>
      </div>
      <p class="tagline">Computer Training for Educators</p>
    </header>
    <div class="header-rule"></div>

    <div class="grass" role="img" aria-label="Green grass growing along the foot of the page"></div>

    <footer class="contact">
      <div class="phone">0508 PCS MENTOR</div>
      <div class="phone">021 839 415</div>
      <div>
        <span class="label">web</span><span class="sep">www.crossingthestream.co.nz</span>
        <span class="label">email</span><span>training@crossingthestream.co.nz</span>
      </div>
    </footer>
  </main>
</body>
</html>
```